BildeVOLD buisnesscard

Hey :) I need a modern buisnesscard for my company BildeVOLD
It most have:
Dagligleder og Fotograf: Henrik Audun Strandvik

Mob: +4791264085
Epost: post@bildevold.example
Adresse: Kvernbakken9, 6040 Langevåg

Facbook and instagram logo with text BildeVOLD

BildeVOLD logo

It Company

```html
<!DOCTYPE html>
<html lang="no">
<head>
<meta charset="utf-8">
<title>BildeVOLD – visittkort</title>
<link href="https://fonts.googleapis.com/css2?family=Lato:wght@400;700&display=swap" rel="stylesheet">
<style>
  :root {
    --backdrop: #e9e9ea;
    --card-white: #ffffff;
    --band-black: #0a0a0a;
    --brand-grey: #b9b7b9;
    --text-light: #ffffff;
    --icon-grey: #cfcfcf;
  }
  * { box-sizing: border-box; margin: 0; padding: 0; }
  html, body { width: 1200px; height: 900px; overflow: hidden; }
  body {
    background: var(--backdrop);
    font-family: "Lato", sans-serif;
    position: relative;
  }
  .card {
    position: absolute;
    left: 270px;
    width: 660px;
    height: 380px;
    background: var(--card-white);
    box-shadow: 0 8px 24px rgba(0,0,0,0.18);
    overflow: hidden;
  }
  .card--front { top: 40px; }
  .card--back { top: 480px; }

  .brand-name {
    font-weight: 700;
    color: var(--brand-grey);
    letter-spacing: 1px;
    display: flex;
    align-items: center;
    gap: 16px;
  }
  .brand-name .brand-dot {
    width: 22px; height: 22px; border-radius: 50%;
    background: var(--brand-grey);
    flex: none;
  }
  .card--front .brand-name {
    position: absolute; left: 0; right: 0; top: 150px;
    justify-content: center;
    font-size: 64px;
  }
  .card--back .brand-name {
    position: absolute; left: 34px; top: 66px;
    font-size: 52px;
  }

  .band { position: absolute; inset: 0; width: 100%; height: 100%; }

  .address {
    position: absolute; left: 34px; top: 262px;
    color: var(--text-light);
    font-style: normal;
    font-size: 16px; line-height: 1.35;
  }
  .contact {
    position: absolute; right: 30px; top: 234px;
    color: var(--text-light);
    text-align: right;
  }
  .contact .person { font-size: 22px; letter-spacing: 0.5px; line-height: 1.2; }
  .contact .role { font-size: 16px; margin-bottom: 10px; }
  .contact ul { list-style: none; }
  .contact li {
    font-size: 17px; line-height: 1.22;
    display: flex; justify-content: flex-end; align-items: center; gap: 10px;
  }
  .contact .icon { width: 16px; height: 16px; flex: none; }
  .contact .social-square {
    width: 15px; height: 15px; background: var(--icon-grey); border-radius: 2px; flex: none;
  }
</style>
</head>
<body>
  <section class="card card--front" aria-label="Kortets forside">
    <div class="brand-name"><span class="brand-dot"></span>BildeVOLD</div>
  </section>

  <section class="card card--back" aria-label="Kortets bakside">
    <div class="brand-name"><span class="brand-dot"></span>BildeVOLD</div>

    <svg class="band" viewBox="0 0 660 380" preserveAspectRatio="none" aria-hidden="true">
      <path d="M300 222 C420 214 560 190 660 110 L660 118 C570 192 430 220 300 222 Z" fill="var(--brand-grey)"/>
      <path d="M0 172 C120 215 230 232 320 228 C470 222 590 180 660 128 L660 380 L0 380 Z" fill="var(--band-black)"/>
    </svg>

    <address class="address">Kvernbakken9<br>6040 Fjellvik</address>

    <div class="contact">
      <p class="person">Henrik Audun Strandvik</p>
      <p class="role">Dagligleder og Fotograf</p>
      <ul>
        <li>+4791264085
          <svg class="icon" viewBox="0 0 16 16" aria-hidden="true"><rect x="4" y="1" width="8" height="14" rx="1.5" fill="none" stroke="var(--icon-grey)" stroke-width="1.5"/><circle cx="8" cy="12.5" r="0.9" fill="var(--icon-grey)"/></svg>
        </li>
        <li>post@bildevold.example
          <svg class="icon" viewBox="0 0 16 16" aria-hidden="true"><rect x="1" y="3" width="14" height="10" fill="var(--icon-grey)"/><path d="M1 3 L8 9 L15 3" fill="none" stroke="var(--band-black)" stroke-width="1.2"/></svg>
        </li>
        <li>BildeVOLD <span class="social-square"></span></li>
        <li>BildeVOLD <span class="social-square"></span></li>
      </ul>
    </div>
  </section>
</body>
</html>
```